Tampa Bay fishing guide needs stunning website.

I currently have a site - www.reelcoveguide.net which I personally put together using the Pagely platform and I am looking for a redesign on a different platform (Sitecraft?) that will allow me to easily create landing pages in the future. Would like to have a block for visitors to opt in to newsletter. Need social media links on all pages.

I would like to let my visitors know that I am able to handle their fishing charter needs here in the Tampa Bay area, if I'm not available for the dates they are looking to go I can refer them to a reputable captain in the area.

Target Market(s)

United States

Industry/Entity Type

Tourism

Coding

Coded - Design and coding required

Number of Pages Required

5+ page

Font styles to use
Sans Serif

Colors
0355a3
3176b5
85abd2
fbf289

Requirements
Must have
• Mobile Responsive, Ability to insert Vantor Metrics, Chatterbox pixels, ability to add custom landing pages in future
Nice to have
• Clean, easy navigation

```html
<!DOCTYPE html>
<html lang="en">
<head>
<meta charset="utf-8">
<title>Capt. Dale Harmon – Tampa Bay Fishing Charters</title>
<link href="https://fonts.googleapis.com/css2?family=Open+Sans:wght@400;600;700;800&display=swap" rel="stylesheet">
<style>
:root{
  --blue-deep:#0355a3;
  --blue-mid:#3176b5;
  --blue-soft:#85abd2;
  --yellow:#fbf289;
  --ink:#4a4a4a;
  --navy:#0d3f73;
  --cell:#f2f2f2;
  --line:#dcdcdc;
  --white:#ffffff;
}
*{box-sizing:border-box;margin:0;padding:0}
html,body{width:1200px;height:2769px;overflow:hidden}
body{position:relative;font-family:"Open Sans",Arial,sans-serif;color:var(--ink);background:var(--white)}
.abs{position:absolute}

/* Hero */
.hero{left:0;top:0;width:1200px;height:640px;overflow:hidden}
.hero-photo{position:absolute;inset:0;background:linear-gradient(100deg,#0f5a3c 0%,#1d7a55 30%,#2f8a6a 45%,#8fb2c8 62%,#d8e2ea 75%,#b9c9d6 100%)}
.hero-curve{position:absolute;left:0;bottom:0;width:1200px;height:80px}
.brand{left:74px;top:30px;color:var(--white);font-weight:800;font-size:34px;line-height:1;letter-spacing:.5px}
.brand small{display:block;font-size:14px;font-weight:800;letter-spacing:2px;margin-bottom:4px}
.top-phone{right:74px;top:40px;color:var(--yellow);font-weight:700;font-size:19px;display:flex;align-items:center;gap:8px}
.top-phone b{font-size:25px;font-weight:700}
.main-nav{left:74px;top:114px;width:1052px;height:46px;background:var(--blue-deep);display:flex;align-items:center}
.main-nav a{color:var(--white);text-decoration:none;font-size:14px;font-weight:700;padding:0 25px;height:46px;line-height:46px;text-transform:uppercase}
.main-nav a.active{background:var(--yellow);color:var(--blue-deep)}
.social{margin-left:auto;display:flex;gap:14px;padding-right:18px}
.social span{color:var(--white);font-size:11px;font-weight:700}
.hero-tag{left:74px;top:254px;width:465px;height:175px;background:rgba(251,242,137,.92);padding:18px 24px;color:var(--blue-deep);font-weight:800;font-size:21px;line-height:32px;text-transform:uppercase}
.slider-dots{left:76px;top:482px;display:flex;gap:7px}
.slider-dots i{width:10px;height:10px;border-radius:50%;background:var(--white)}
.slider-dots i:first-child{background:var(--blue-mid)}

/* Intro */
.intro{left:74px;top:688px;width:1052px;text-align:center}
.intro-kicker{font-size:16px;font-weight:700;color:#4a4a4a;text-transform:uppercase}
.intro-title{margin-top:10px;font-size:35px;line-height:46px;font-weight:700;color:var(--blue-deep);letter-spacing:9px;text-transform:uppercase}
.intro p{font-size:15px;line-height:24px;margin-top:18px}
.intro p + p{margin-top:10px}
.intro a{color:var(--blue-deep);font-weight:700}

/* Services */
.services{left:0;top:1040px;width:1200px;height:400px;overflow:hidden}
.services-photo{position:absolute;inset:0;background:linear-gradient(180deg,#1c4f86 0%,#2a68a5 45%,#2f70b0 100%)}
.services-curve{position:absolute;left:0;top:0;width:1200px;height:70px}
.services h2{position:absolute;top:42px;width:100%;text-align:center;color:var(--white);font-size:27px;font-weight:700;text-transform:uppercase}
.service{position:absolute;top:108px;width:340px;text-align:center;color:var(--white)}
.service .disc{width:110px;height:110px;border-radius:50%;background:var(--yellow);margin:0 auto;display:flex;align-items:center;justify-content:center}
.service h3{margin-top:32px;font-size:17px;font-weight:700;text-transform:uppercase}
.service p{margin-top:12px;font-size:15px;line-height:24px}

/* Calendar */
.avail-title{left:0;top:1478px;width:1200px;text-align:center;font-size:27px;font-weight:700;color:var(--blue-deep);text-transform:uppercase}
.calendar{left:254px;top:1551px;width:692px;border:1px solid var(--line)}
.cal-head{height:53px;background:var(--yellow);display:flex;align-items:center;justify-content:space-between;padding:0 18px;color:var(--blue-deep);font-weight:700;font-size:17px}
.cal-grid{display:grid;grid-template-columns:repeat(7,1fr)}
.cal-grid .dow{height:30px;line-height:30px;background:var(--blue-soft);color:var(--white);font-size:12px;font-weight:700;text-align:center}
.cal-grid .day{height:52px;line-height:52px;text-align:center;font-size:12px;font-weight:700;color:#333;background:var(--cell);border-right:1px solid var(--line);border-bottom:1px solid var(--line)}
.cal-grid .day.open{background:var(--blue-mid);color:var(--white)}
.cal-grid .day.booked{background:var(--yellow)}
.cal-grid .day.blank{background:var(--cell)}
.legend{left:0;top:1962px;width:1200px;display:flex;justify-content:center;gap:40px;font-size:13px;font-weight:700;color:#444}
.legend span{display:flex;align-items:center;gap:16px}
.legend i{width:30px;height:22px;display:block}

/* Charters */
.charters{left:0;top:2032px;width:1200px;height:362px;background:var(--blue-soft)}
.charters-photo{position:absolute;left:0;top:0;width:522px;height:362px;background:linear-gradient(160deg,#6f94b4 0%,#5c7f9c 40%,#8fa7b6 70%,#c9cfd2 100%)}
.charters-copy{position:absolute;left:585px;top:64px;width:540px;color:var(--white)}
.charters-copy h2{font-size:27px;font-weight:700;text-transform:uppercase}
.charters-copy p{margin-top:16px;font-size:17px;line-height:31px;color:#f4f7fb}
.btn{display:inline-block;background:var(--yellow);color:var(--blue-deep);font-weight:700;font-size:15px;text-transform:uppercase;text-decoration:none;text-align:center}
.charters-copy .btn{margin-top:46px;width:220px;height:42px;line-height:42px}

/* Newsletter */
.newsletter{left:0;top:2394px;width:1200px;height:110px}
.newsletter h2{position:absolute;left:155px;top:33px;font-size:27px;font-weight:700;color:var(--blue-deep);text-transform:uppercase}
.newsletter .field{position:absolute;left:476px;top:34px;width:342px;height:40px;border:1px solid #bbb;padding:0 12px;line-height:38px;font-size:13px;color:#333}
.newsletter .btn{position:absolute;left:825px;top:34px;width:220px;height:40px;line-height:40px}

/* Footer */
.footer{left:0;top:2504px;width:1200px;height:265px;background:var(--blue-deep);color:var(--white)}
.fcol{position:absolute;top:36px;font-size:13px;line-height:26px}
.fcol h4{color:var(--yellow);font-size:15px;font-weight:700;text-transform:uppercase;margin-bottom:4px;line-height:24px}
.fcol .row{display:flex;align-items:center;gap:8px}
.cards{display:flex;gap:8px;margin-top:8px}
.cards span{width:40px;height:26px;background:var(--white);color:var(--blue-deep);font-size:8px;font-weight:700;line-height:26px;text-align:center}
.footer-brand{margin-top:16px;font-size:17px;font-weight:800}
.copyright{font-size:11px;line-height:18px;margin-top:10px}
</style>
</head>
<body>

<header class="hero abs">
  <div class="hero-photo" role="img" aria-label="Photo of anglers on a boat holding a large tarpon over green bay water"></div>
  <svg class="hero-curve" viewBox="0 0 1200 80" preserveAspectRatio="none"><path d="M0 20 Q600 110 1200 0 L1200 80 L0 80 Z" fill="#ffffff"/></svg>
  <div class="brand abs"><small>CAPT. DALE</small>Harmon</div>
  <div class="top-phone abs">
    <svg width="16" height="16" viewBox="0 0 24 24"><path d="M6.6 10.8a15 15 0 0 0 6.6 6.6l2.2-2.2c.3-.3.7-.4 1-.2 1.1.4 2.3.6 3.6.6.6 0 1 .4 1 1V20c0 .6-.4 1-1 1A17 17 0 0 1 3 4c0-.6.4-1 1-1h3.5c.6 0 1 .4 1 1 0 1.3.2 2.5.6 3.6.1.3 0 .7-.2 1z" fill="#fbf289"/></svg>
    Call Capt. Dale <b>(555) 204-7788</b>
  </div>
  <nav class="main-nav abs">
    <a class="active" href="#">Home</a>
    <a href="#">About Us</a>
    <a href="#">Pick Up Locations</a>
    <a href="#">Rates</a>
    <a href="#">Contact Us</a>
    <a href="#">Gift Card</a>
    <div class="social"><span>Chatterbox</span><span>Chirp</span><span>Orbit</span><span>Linkr</span><span>Reelz</span></div>
  </nav>
  <div class="hero-tag abs">Come fish with Tampa Bay, FL fishing guide, Tampa Bay fishing charter most respected captain, 25 year native guide</div>
  <div class="slider-dots abs"><i></i><i></i><i></i><i></i></div>
</header>

<section class="intro abs">
  <div class="intro-kicker">Tampa Bay Fishing Charters Florida | Fishing Charters Tampa Bay</div>
  <h1 class="intro-title">Tampa Bay, Fishing Guide, Tampa Bay<br>Fishing Charters</h1>
  <p>Capt. Dale Harmon, with over 20 years' experience, Native fishing charter tampa charter captain offering full and half day fishing charters on the waters of Tampa Bay. If you're looking for a great fishing charter tampa don't hesitate to contact Capt. Dale or you can simply book your trip online <a href="#">Here</a>.</p>
  <p>Come enjoy a wonderful day fishing charters Tampa for Tarpon, Snook, Redfish, Trout, Sharks, Cobia, Spanish mackerel as well as others aboard Capt. Dale Harmon Sport fishing Charters boat. Capt. Dale will work hard to ensure that you and your guests have a memorable day enjoying the wonderful gamefish that Tampa Bay has to offer.</p>
</section>

<section class="services abs">
  <div class="services-photo" role="img" aria-label="Blue-tinted photo of anglers landing a fish over rippling water"></div>
  <svg class="services-curve" viewBox="0 0 1200 70" preserveAspectRatio="none"><path d="M0 0 L1200 0 L1200 60 Q600 -40 0 60 Z" fill="#ffffff"/></svg>
  <h2>Our Services</h2>
  <div class="service" style="left:70px">
    <div class="disc"><svg width="48" height="48" viewBox="0 0 48 48" fill="none" stroke="#3176b5" stroke-width="3.5" stroke-linecap="round"><path d="M26 6v22a8 8 0 0 1-16 0v-4l-4 4"/><circle cx="26" cy="5" r="2"/></svg></div>
    <h3>Fishing Guide</h3>
    <p>Lorem ipsum dolor sit amet, consect- etuer adipiscing elit, sed diam nonummy nibh euismod tincidunt ut laoreet..</p>
  </div>
  <div class="service" style="left:430px">
    <div class="disc"><svg width="56" height="48" viewBox="0 0 56 48" fill="#0355a3"><rect x="18" y="10" width="16" height="10"/><path d="M6 22h44l-6 12H12z"/><path d="M4 40q6-4 12 0t12 0 12 0 12 0" stroke="#0355a3" stroke-width="3" fill="none"/></svg></div>
    <h3>Fishing Charters</h3>
    <p>Lorem ipsum dolor sit amet, consect- etuer adipiscing elit, sed diam nonummy nibh euismod tincidunt ut laoreet..</p>
  </div>
  <div class="service" style="left:790px">
    <div class="disc"><svg width="34" height="46" viewBox="0 0 24 32"><path d="M12 0a11 11 0 0 0-11 11c0 8 11 21 11 21s11-13 11-21A11 11 0 0 0 12 0zm0 15a4 4 0 1 1 0-8 4 4 0 0 1 0 8z" fill="#0355a3"/></svg></div>
    <h3>Multiple Pickup Points</h3>
    <p>Lorem ipsum dolor sit amet, consect- etuer adipiscing elit, sed diam nonummy nibh euismod tincidunt ut laoreet..</p>
  </div>
</section>

<h2 class="avail-title abs">Check Availability Fishing Charter</h2>
<div class="calendar abs">
  <div class="cal-head">
    <svg width="14" height="18" viewBox="0 0 14 18"><path d="M11 2 4 9l7 7" stroke="#333" stroke-width="3" fill="none"/></svg>
    <span>OCTOBER 2016</span>
    <svg width="14" height="18" viewBox="0 0 14 18"><path d="m3 2 7 7-7 7" stroke="#333" stroke-width="3" fill="none"/></svg>
  </div>
  <div class="cal-grid">
    <div class="dow">M</div><div class="dow">T</div><div class="dow">W</div><div class="dow">T</div><div class="dow">F</div><div class="dow">S</div><div class="dow">S</div>
    <div class="day blank"></div><div class="day blank"></div><div class="day blank"></div><div class="day blank"></div><div class="day blank"></div><div class="day blank"></div><div class="day">1</div>
    <div class="day open">2</div><div class="day">3</div><div class="day open">4</div><div class="day open">5</div><div class="day open">6</div><div class="day">7</div><div class="day open">8</div>
    <div class="day">9</div><div class="day">10</div><div class="day">11</div><div class="day">12</div><div class="day booked">13</div><div class="day booked">14</div><div class="day">15</div>
    <div class="day">16</div><div class="day booked">17</div><div class="day open">18</div><div class="day">19</div><div class="day">20</div><div class="day">21</div><div class="day open">22</div>
    <div class="day">23</div><div class="day">24</div><div class="day booked">25</div><div class="day">26</div><div class="day">27</div><div class="day">28</div><div class="day">29</div>
    <div class="day">30</div><div class="day">31</div><div class="day blank"></div><div class="day blank"></div><div class="day blank"></div><div class="day blank"></div><div class="day blank"></div>
  </div>
</div>
<div class="legend abs">
  <span><i style="background:var(--blue-mid)"></i>Available</span>
  <span><i style="background:var(--yellow)"></i>Unavailable</span>
</div>

<section class="charters abs">
  <div class="charters-photo" role="img" aria-label="Photo of two anglers on a boat holding up a tarpon"></div>
  <div class="charters-copy">
    <h2>Full &amp; Half Day Charters</h2>
    <p>Offering Tampa Bay, FL fishing charters on the beautiful waters of Tampa Bay. Fish with Capt. Dale Harmon, Tampa Bay, FL fishing guide for over 20 years</p>
    <a class="btn" href="#">Find Out More</a>
  </div>
</section>

<section class="newsletter abs">
  <h2>Newsletter Signup</h2>
  <div class="field">Enter Email Address</div>
  <a class="btn" href="#">Sign Up Now</a>
</section>

<footer class="footer abs">
  <div class="fcol" style="left:74px">
    <h4>Quick Links</h4>
    <div>Home</div><div>About Us</div><div>Pick Up Locations</div><div>Rates</div><div>Contact Us</div><div>Gift Card</div>
  </div>
  <div class="fcol" style="left:323px">
    <h4>Pickup Locations</h4>
    <div>Harborview Marina - St. Petersburg</div><div>Pelican Cove - Ruskin</div><div>Bayside Boat Ramp</div><div>Mullet Point Ramp</div>
  </div>
  <div class="fcol" style="left:615px">
    <h4>Contact Us</h4>
    <div class="row"><svg width="12" height="12" viewBox="0 0 24 24"><path d="M6.6 10.8a15 15 0 0 0 6.6 6.6l2.2-2.2c.3-.3.7-.4 1-.2 1.1.4 2.3.6 3.6.6.6 0 1 .4 1 1V20c0 .6-.4 1-1 1A17 17 0 0 1 3 4c0-.6.4-1 1-1h3.5c.6 0 1 .4 1 1 0 1.3.2 2.5.6 3.6.1.3 0 .7-.2 1z" fill="#fff"/></svg>555-204-7788</div>
    <div class="row"><svg width="13" height="10" viewBox="0 0 26 20"><rect width="26" height="20" rx="2" fill="#fff"/><path d="M1 2l12 9 12-9" stroke="#0355a3" stroke-width="2.5" fill="none"/></svg>captdale@reelcovemail.net</div>
    <h4 style="margin-top:12px">Follow Us</h4>
    <div class="row" style="gap:12px;font-size:11px;font-weight:700"><span>Chatterbox</span><span>Chirp</span><span>Orbit</span><span>Linkr</span><span>Reelz</span></div>
  </div>
  <div class="fcol" style="left:890px">
    <h4>We Accept</h4>
    <div class="cards"><span>PayLink</span><span>CardOne</span><span>Centra</span><span>Vesta</span></div>
    <div class="footer-brand">Capt. Dale Harmon</div>
    <div class="copyright">Copyright © 2016 Capt. Dale Harmon<br>All Right Reserved</div>
  </div>
</footer>

</body>
</html>
```